Homeowners Insurance Provider Website

We are selling homeowners insurance policy / tenants Policy/Flood Insurance in USA in few states and planning expand nationally.

Our target audience are two folds: Customers (Buy policies) and Insurance Agents who wants to work with us to sell our policies to customers. But website should focus 80% on customers and 20% on agents. So, more customer focused user experience. Please note that there is no direct buy option for customers. They always go through insurance agents.

Customer focused, educational that makes buyer journey easy. We don’t want to come off as trying sell something as there is no direct sales involved from website.

Target Market(s)

Homeowners in USA and Insurance agent who sells these insurance.

Industry/Entity Type

Insurance

Number of Pages Required

4 page

Font styles to use
Other font styles liked:
• Open to suggestions

Colors

Designer to choose colors to be used in the design.

Requirements
Must have
• Three most important things: Trustworthy, Authentic, Simple
• Please use colors form logo and grays
• We like: www.hollowmere.com
• https://www.quillfenbrook.com/
• We need Agent Look up tool on home page similar to what is shown on example sites.
• Design:
• Home Page - Open to Ideas
• Insurance (Products) Landing Page - Info similar to: https://www.quillfenbrook.com/insurance/
• Agents Page - https://www.quillfenbrook.com/agents/
• Claims Page - Information similar to: https://www.quillfenbrook.com/claims-center/
• Site Navigation:
• Home
• Insurance
• Claims
• Agents
• About Us
• Contact Us
Nice to have
• Elegant, minimal and clean design that reflects trust and authenticity.
Should not have
• Slider or rotating images - prefer flat design. Not over powering design.

```html
<!DOCTYPE html>
<html lang="en">
<head>
<meta charset="utf-8">
<title>Homeowners Insurance Co.</title>
<link href="https://fonts.googleapis.com/css2?family=Cabin:wght@400;500;600&family=Open+Sans:wght@400;600&display=swap" rel="stylesheet">
<style>
:root{
  --navy:#1f3a7a;
  --navy-dark:#17306a;
  --red:#d0142c;
  --gray-bg:#ededed;
  --card-gray:#efefef;
  --text:#333;
  --muted:#666;
  --line:#dcdcdc;
  --footer:#2a2a2a;
}
*{box-sizing:border-box;margin:0;padding:0}
html,body{width:1200px;height:3734px;overflow:hidden}
body{font-family:"Open Sans",Arial,sans-serif;color:var(--text);background:#fff;position:relative}
.sec{position:absolute;left:0;width:1200px}
h2.title{font-family:"Cabin",Arial,sans-serif;font-weight:500;color:var(--red);font-size:34px;text-align:center;letter-spacing:.5px}

/* header */
.header{top:0;height:115px;border-top:4px solid var(--navy);background:#fff}
.brand{position:absolute;left:78px;top:32px;display:flex;align-items:center;gap:14px}
.brand-mark{width:46px;height:46px;background:var(--navy)}
.brand-name{font-family:"Cabin",Arial,sans-serif;font-weight:600;font-size:22px;line-height:24px;color:var(--navy);width:220px}
.nav{position:absolute;right:50px;top:0;display:flex;height:111px}
.nav a{display:flex;align-items:center;padding:0 24px;font-size:16px;color:#444;text-decoration:none;text-transform:uppercase}
.nav a.active{background:var(--navy);color:#fff}

/* hero */
.hero{top:115px;height:607px;clip-path:polygon(0 0,100% 0,100% 88%,0 100%)}
.hero-photo{position:absolute;inset:0;background:linear-gradient(120deg,#5a534c,#3d3a38 45%,#6b6257)}
.hero-shade{position:absolute;inset:0;background:rgba(20,20,20,.35)}
.hero-text{position:absolute;top:225px;left:200px;width:800px;text-align:center;color:#fff}
.hero-text h1{font-family:"Cabin",Arial,sans-serif;font-weight:500;font-size:40px;letter-spacing:.5px}
.hero-text p{font-size:15px;line-height:27px;margin-top:16px}

/* welcome */
.welcome{top:722px;height:486px}
.welcome h2{margin-top:50px}
.welcome .intro{width:860px;margin:26px auto 0;text-align:center;font-size:14px;line-height:25px;color:var(--muted)}
.steps{position:absolute;top:240px;left:0;width:1200px;height:220px}
.step{position:absolute;width:260px;text-align:center}
.step .ring{width:118px;height:118px;border-radius:50%;border:6px solid #eee;margin:0 auto;display:flex;align-items:center;justify-content:center;box-shadow:0 2px 6px rgba(0,0,0,.12);background:#fff}
.step .ring svg{width:60px;height:60px}
.step span{display:block;margin-top:34px;font-size:21px;color:#222}
.dots{position:absolute;top:40px}

/* products */
.products{top:1208px;height:440px;background:var(--gray-bg)}
.products h2{margin-top:40px}
.prod-row{position:absolute;top:102px;left:75px;display:flex;gap:37px}
.prod{width:236px;height:272px;background:#fff;border:1px solid #ddd;padding:10px;text-align:center}
.prod .ph{height:135px}
.prod h3{font-family:"Cabin",Arial,sans-serif;font-weight:400;font-size:21px;margin-top:18px;color:#222}
.prod p{font-size:14px;line-height:23px;color:var(--muted);margin-top:6px}

/* testimonials */
.clients{top:1648px;height:456px}
.clients h2{margin-top:42px}
.quote-row{position:absolute;top:156px;left:75px;display:flex;gap:40px}
.quote{position:relative;width:323px;height:220px;background:var(--card-gray);border-radius:14px;padding:40px 25px 0;box-shadow:0 3px 5px rgba(0,0,0,.12)}
.quote .badge{position:absolute;right:35px;top:-34px;width:80px;height:80px;border-radius:50%;background:var(--navy);border:5px solid #fff;display:flex;align-items:center;justify-content:center}
.quote h3{font-family:"Cabin",Arial,sans-serif;font-weight:400;font-size:21px;color:#333}
.quote .rule{width:60px;height:3px;background:var(--navy);margin:14px 0 18px}
.quote p{font-size:14px;line-height:24px;color:var(--muted)}

/* quote form */
.get-quote{top:2104px;height:493px}
.gq-photo{position:absolute;left:0;top:0;width:760px;height:493px;background:linear-gradient(110deg,#5c4a3c,#9a8a78 45%,#cfc7bc)}
.gq-panel{position:absolute;left:685px;top:0;width:515px;height:493px;background:rgba(31,58,122,.88);clip-path:polygon(0 0,100% 0,100% 100%,0 100%)}
.gq-panel h2{position:absolute;left:52px;top:92px;font-family:"Cabin",Arial,sans-serif;font-weight:500;font-size:30px;color:#fff}
.gq-field{position:absolute;left:52px;width:385px;height:40px;border:1px solid rgba(255,255,255,.8);color:#fff;font-size:13px;padding:11px 12px}
.gq-btn{position:absolute;left:52px;top:348px;width:146px;height:46px;background:#fff;color:var(--navy);font-family:"Cabin",Arial,sans-serif;font-size:19px;font-weight:500;display:flex;align-items:center;justify-content:center}

/* team */
.team{top:2597px;height:510px}
.team h2{margin-top:40px}
.team-row{position:absolute;top:97px;left:75px;display:flex;gap:37px}
.member{width:241px;height:324px;border:1px solid #ddd;padding:15px;text-align:center}
.member.featured{border:2px solid var(--red)}
.member .ph{height:210px;background:linear-gradient(160deg,#d9dde0,#9aa3ab)}
.member h3{font-family:"Cabin",Arial,sans-serif;font-weight:400;font-size:20px;margin-top:20px;color:#222}
.member p{font-size:14px;color:var(--muted);margin-top:6px}
.member .rule{width:48px;height:2px;background:#333;margin:14px auto 0}

/* subscribe */
.subscribe{top:3107px;height:105px;background:var(--navy)}
.subscribe p{position:absolute;left:78px;top:37px;font-family:"Cabin",Arial,sans-serif;font-size:25px;color:#fff}
.sub-input{position:absolute;left:695px;top:34px;width:290px;height:40px;background:var(--navy-dark);color:#fff;font-size:13px;font-style:italic;padding:11px 14px}
.sub-btn{position:absolute;left:997px;top:34px;width:125px;height:40px;background:#2c4a92;color:#fff;font-size:15px;display:flex;align-items:center;justify-content:center;font-weight:600}

/* contact */
.contact{top:3212px;height:398px}
.ct-photo{position:absolute;inset:0;background:linear-gradient(120deg,#8d8579,#b7b2a9 40%,#9c958c)}
.ct-shade{position:absolute;inset:0;background:rgba(255,255,255,.45)}
.ct-detail{position:absolute;left:75px;top:65px;width:311px;height:309px;border:1px solid #555;padding:36px 22px}
.ct-detail h3{font-family:"Cabin",Arial,sans-serif;font-weight:500;font-size:20px;color:#222}
.ct-detail .rule{height:1px;background:#777;margin:14px 0 22px}
.ct-item{display:flex;gap:14px;font-size:15px;line-height:23px;color:#222;margin-bottom:16px}
.ct-item svg{flex:none;width:18px;height:20px;margin-top:2px}
.cf-title{position:absolute;left:443px;top:66px;font-family:"Cabin",Arial,sans-serif;font-weight:500;font-size:31px;color:#222}
.cf-rule{position:absolute;left:443px;top:118px;width:672px;height:1px;background:#666}
.cf-field{position:absolute;left:448px;width:282px;height:40px;background:rgba(255,255,255,.8);font-size:13px;font-style:italic;color:#888;padding:10px 12px}
.cf-msg{position:absolute;left:742px;top:164px;width:303px;height:144px;background:rgba(255,255,255,.8);font-size:13px;font-style:italic;color:#888;padding:10px 12px}
.cf-send{position:absolute;left:1061px;top:164px;width:61px;height:144px;background:var(--red);display:flex;align-items:center;justify-content:center}

/* footer */
.footer{top:3610px;height:124px;background:var(--footer);color:#fff;text-align:center}
.footer nav{margin-top:30px;display:flex;justify-content:center;gap:38px;font-size:15px}
.footer p{font-size:14px;margin-top:30px;color:#eee}
</style>
</head>
<body>

<header class="sec header">
  <div class="brand"><div class="brand-mark"></div><div class="brand-name">HOMEOWNERS<br>INSURANCE CO.</div></div>
  <nav class="nav">
    <a class="active">Home</a><a>About</a><a>Insurance</a><a>Claims</a><a>Agents</a><a>Contact</a>
  </nav>
</header>

<section class="sec hero">
  <div class="hero-photo" role="img" aria-label="Family sitting together on a sofa at home"></div>
  <div class="hero-shade"></div>
  <div class="hero-text">
    <h1>HOMEOWNERS INSURANCE CO.</h1>
    <p>Lorem Ipsum is simply dummy text of the printing and typesetting industry. Lorem Ipsum has been the industry's standard dummy text ever since the 1500s, when an unknown printer took a galley of type and scrambled it to make a type specimen book. It has</p>
  </div>
</section>

<section class="sec welcome">
  <h2 class="title">WELCOME VISITOR!</h2>
  <p class="intro">Lorem ipsum dolor sit amet, consectetur adipiscing elit. Nam tempor faucibus ante, eget vulputate libero pharetra eu. Nulla at felis eros. Sed ut metus justo. Suspendisse vestibulum dui at magna rutrum vestibulum. Vestibulum ante ipsum primis in faucibus orci luctus et ultrices posuere cubilia Curae; Nullam eget blandit augue.</p>
  <div class="steps">
    <div class="step" style="left:110px">
      <div class="ring"><svg viewBox="0 0 60 60" fill="none" stroke="#1f3a7a" stroke-width="4"><path d="M20 30 30 21 40 30M24 28v10h12V28"/><path d="M8 36c4 6 10 10 16 12M52 36c-4 6-10 10-16 12"/></svg></div>
      <span>homeowners insurance</span>
    </div>
    <svg class="dots" style="left:340px" width="180" height="30" viewBox="0 0 180 30" fill="none" stroke="#bbb" stroke-width="2" stroke-dasharray="3 5"><path d="M5 20Q90 35 170 12"/><path d="M163 8l8 4-6 6" stroke-dasharray="none"/></svg>
    <div class="step" style="left:470px">
      <div class="ring"><svg viewBox="0 0 60 60" fill="none" stroke="#1f3a7a" stroke-width="4"><path d="M12 28 30 12 48 28"/><path d="M18 26v14h24V26"/><path d="M10 44c8 6 32 6 40 0"/></svg></div>
      <span>Tenants Policy</span>
    </div>
    <svg class="dots" style="left:700px" width="180" height="30" viewBox="0 0 180 30" fill="none" stroke="#bbb" stroke-width="2" stroke-dasharray="3 5"><path d="M5 20Q90 35 170 12"/><path d="M163 8l8 4-6 6" stroke-dasharray="none"/></svg>
    <div class="step" style="left:830px">
      <div class="ring"><svg viewBox="0 0 60 60" fill="none" stroke="#1f3a7a" stroke-width="4"><path d="M14 28 30 14 46 28"/><path d="M20 26v12h20V26"/><path d="M26 38v-7h8v7"/><path d="M10 46q5-4 10 0t10 0 10 0 10 0"/></svg></div>
      <span>Flood Insurance</span>
    </div>
  </div>
</section>

<section class="sec products">
  <h2 class="title">OUR PRODUCTS</h2>
  <div class="prod-row">
    <div class="prod"><div class="ph" role="img" aria-label="Family walking in front of their house" style="background:linear-gradient(160deg,#7d8a6a,#4f5a3e)"></div><h3>Homeowners</h3><p>Lorem Ipsum is simply dummy text of the printing.</p></div>
    <div class="prod"><div class="ph" role="img" aria-label="Couple moving boxes into an apartment" style="background:linear-gradient(160deg,#d8d2c8,#a89a8c)"></div><h3>Renters/Condo</h3><p>Lorem Ipsum is simply dummy text of the printing.</p></div>
    <div class="prod"><div class="ph" role="img" aria-label="House on fire" style="background:linear-gradient(160deg,#8a8f96,#b05a2c)"></div><h3>Dwelling Fire</h3><p>Lorem Ipsum is simply dummy text of the printing.</p></div>
    <div class="prod"><div class="ph" role="img" aria-label="Hands typing on a laptop" style="background:linear-gradient(160deg,#3b3550,#a37a86)"></div><h3>Agent Locator Tool</h3><p>Lorem Ipsum is simply dummy text of the printing.</p></div>
  </div>
</section>

<section class="sec clients">
  <h2 class="title">WHAT OUR CLIENTS SAY</h2>
  <div class="quote-row">
    <div class="quote"><div class="badge"><svg width="34" height="28" viewBox="0 0 34 28" fill="#fff"><path d="M2 28V16C2 7 7 2 14 0l1 4c-4 2-6 5-6 9h6v15zM19 28V16c0-9 5-14 12-16l1 4c-4 2-6 5-6 9h6v15z"/></svg></div><h3>Client Name</h3><div class="rule"></div><p>Lorem Ipsum is simply dummy text of the printing and typesetting industry. Lorem Ipsum has been the industry.</p></div>
    <div class="quote"><div class="badge"><svg width="34" height="28" viewBox="0 0 34 28" fill="#fff"><path d="M2 28V16C2 7 7 2 14 0l1 4c-4 2-6 5-6 9h6v15zM19 28V16c0-9 5-14 12-16l1 4c-4 2-6 5-6 9h6v15z"/></svg></div><h3>Client Name</h3><div class="rule"></div><p>Lorem Ipsum is simply dummy text of the printing and typesetting industry. Lorem Ipsum has been the industry.</p></div>
    <div class="quote"><div class="badge"><svg width="34" height="28" viewBox="0 0 34 28" fill="#fff"><path d="M2 28V16C2 7 7 2 14 0l1 4c-4 2-6 5-6 9h6v15zM19 28V16c0-9 5-14 12-16l1 4c-4 2-6 5-6 9h6v15z"/></svg></div><h3>Client Name</h3><div class="rule"></div><p>Lorem Ipsum is simply dummy text of the printing and typesetting industry. Lorem Ipsum has been the industry.</p></div>
  </div>
</section>

<section class="sec get-quote">
  <div class="gq-photo" role="img" aria-label="Agent reviewing a policy with a young couple"></div>
  <div class="gq-panel">
    <h2>GET IN INSURANCE QUOTE</h2>
    <div class="gq-field" style="top:158px">Name</div>
    <div class="gq-field" style="top:215px">Email</div>
    <div class="gq-field" style="top:272px">Phone no.</div>
    <div class="gq-btn">SEND</div>
  </div>
</section>

<section class="sec team">
  <h2 class="title">OUR TEAM</h2>
  <div class="team-row">
    <div class="member featured"><div class="ph" role="img" aria-label="Team member portrait"></div><h3>Surname Name</h3><p>Lorem Ipsum is simply.</p><div class="rule"></div></div>
    <div class="member"><div class="ph" role="img" aria-label="Team member portrait"></div><h3>Surname Name</h3><p>Lorem Ipsum is simply.</p><div class="rule"></div></div>
    <div class="member"><div class="ph" role="img" aria-label="Team member portrait"></div><h3>Surname Name</h3><p>Lorem Ipsum is simply.</p><div class="rule"></div></div>
    <div class="member"><div class="ph" role="img" aria-label="Team member portrait"></div><h3>Surname Name</h3><p>Lorem Ipsum is simply.</p><div class="rule"></div></div>
  </div>
</section>

<section class="sec subscribe">
  <p>To get latest updates and promotions signup now!</p>
  <div class="sub-input">Enter Your Email</div>
  <div class="sub-btn">SUBSCRIBE</div>
</section>

<section class="sec contact">
  <div class="ct-photo" role="img" aria-label="Family outside a suburban house"></div>
  <div class="ct-shade"></div>
  <div class="ct-detail">
    <h3>CONTACT DETAIL</h3><div class="rule"></div>
    <div class="ct-item"><svg viewBox="0 0 18 20" fill="none" stroke="#d0142c" stroke-width="2"><path d="M9 19s6-6 6-11A6 6 0 0 0 3 8c0 5 6 11 6 11z"/><circle cx="9" cy="8" r="2"/></svg><span>Lorem Ipsum is simply<br>dummy text of the printing.</span></div>
    <div class="ct-item"><svg viewBox="0 0 18 20" fill="#d0142c"><path d="M4 2l3 4-2 2c1 2 3 4 5 5l2-2 4 3-2 3C8 17 2 10 2 4z"/></svg><span>123 456 7890</span></div>
    <div class="ct-item"><svg viewBox="0 0 18 20" fill="none" stroke="#d0142c" stroke-width="2"><rect x="2" y="5" width="14" height="10"/><path d="M2 5l7 6 7-6"/></svg><span>info@brackenhome.com</span></div>
  </div>
  <div class="cf-title">CONTACT FORM</div>
  <div class="cf-rule"></div>
  <div class="cf-field" style="top:164px">Name</div>
  <div class="cf-field" style="top:216px">Email</div>
  <div class="cf-field" style="top:268px">Phone</div>
  <div class="cf-msg">Message</div>
  <div class="cf-send"><svg width="26" height="26" viewBox="0 0 26 26" fill="#fff"><path d="M2 12 24 2 16 24 12 14z"/></svg></div>
</section>

<footer class="sec footer">
  <nav><span>Home</span><span>About</span><span>Insurance</span><span>Claims</span><span>Agents</span><span>Contact</span></nav>
  <p>©HARROWGATE FUND SOLUTIONS- 2018. All Rights Reserved. | Privacy policy | Terms and Conditions.</p>
</footer>

</body>
</html>
```